Building Design company needing a letterhead

We need a letter head for our Building Design company to send letters etc. to our clients, consultants, councils etc. We would like to see our logo used and company colours. I have attached our style guide and an example of our current letterheads. Top left we would like our logo, top right we would like the company details and at the footer we would like some sort of image/design etc. that suits our brand. I like the Tarrow Design letterhead attached.

Target Market(s)

Professionals, Councils, Consultants, Mums & Dads

Industry/Entity Type

Architecture

Other font styles liked:
• refer the design style guide

Colors
f37122
000000
1b1b1b

Requirements
Must have
• Must have the minimum of a logo, company details and footer
Nice to have
• An image/design made for the footer that would suite our brand and website at www.corvanplans.com.au. Also it would be nice to include the KMEOT logo somewhere perhaps included in the footer.
Should not have
• Large images in the header. I just want the logo and company details.

```html
<!DOCTYPE html>
<html lang="en">
<head>
<meta charset="utf-8">
<title>Corvan Design Letterhead</title>
<link href="https://fonts.googleapis.com/css2?family=Michroma&family=Titillium+Web:wght@400;700&display=swap" rel="stylesheet">
<style>
  :root {
    --brand-orange: #e65a26;
    --ink: #1b1b1b;
    --paper: #ffffff;
    --surround: #878787;
    --watermark: #f0f0f0;
  }
  * { margin: 0; padding: 0; box-sizing: border-box; }
  html, body { width: 847px; height: 1200px; overflow: hidden; background: var(--surround); }
  .letterhead {
    position: absolute; left: 70px; top: 70px;
    width: 708px; height: 1059px;
    background: var(--brand-orange);
    font-family: "Michroma", sans-serif;
    overflow: hidden;
  }
  .letterhead__sheet { position: absolute; inset: 0; }
  .contact {
    position: absolute; left: 25px; top: 27px;
    list-style: none; color: var(--paper);
    font-size: 8.4px; letter-spacing: 0.9px; font-variant: small-caps; text-transform: lowercase;
  }
  .contact li { display: flex; align-items: center; height: 17px; }
  .contact svg { width: 9px; height: 9px; margin-right: 7px; fill: none; stroke: var(--paper); stroke-width: 1.2; }
  .brand {
    position: absolute; left: 268px; top: 60px;
    display: flex; align-items: center; gap: 9px;
  }
  .brand__mark { width: 22px; height: 22px; background: var(--brand-orange); }
  .brand__name {
    color: var(--ink); font-size: 15px; line-height: 21px; letter-spacing: 1px;
  }
  .signatory {
    position: absolute; right: 26px; top: 41px; text-align: right;
    color: var(--paper); font-variant: small-caps; text-transform: lowercase;
  }
  .signatory__name { font-size: 10px; letter-spacing: 1.4px; }
  .signatory__role { font-size: 8.4px; letter-spacing: 1.2px; margin-top: 2px; }
  .watermark {
    position: absolute; left: 354px; top: 540px;
    transform: translate(-50%, -50%) rotate(-45deg);
    color: var(--watermark); font-size: 62px; line-height: 82px;
    letter-spacing: 4px; white-space: nowrap; text-align: center;
  }
  .address {
    position: absolute; left: 0; right: 0; top: 1002px; text-align: center;
    color: var(--paper); font-size: 8.4px; letter-spacing: 1.4px; line-height: 17px;
    font-variant: small-caps; text-transform: lowercase;
  }
</style>
</head>
<body>
  <main class="letterhead">
    <svg class="letterhead__sheet" width="708" height="1059" viewBox="0 0 708 1059" aria-hidden="true">
      <polygon points="0,147 364,16 708,147 708,910 364,987 0,910" fill="var(--paper)"/>
    </svg>

    <div class="watermark" aria-hidden="true">CORVAN<br>DESIGN</div>

    <ul class="contact">
      <li><svg viewBox="0 0 10 10"><path d="M2.5 1 L4 1 L4.5 3 L3.5 4 Q4.5 6 6 6.5 L7 5.5 L9 6 L9 7.5 Q8.5 9 7 9 Q1 7.5 1 2.5 Q1 1 2.5 1Z"/></svg>(123) 456-7890</li>
      <li><svg viewBox="0 0 10 10"><rect x="1" y="2" width="8" height="6"/><path d="M1 2 L5 5.5 L9 2"/></svg>info@companyname.com</li>
      <li><svg viewBox="0 0 10 10"><circle cx="5" cy="5" r="4"/><ellipse cx="5" cy="5" rx="1.8" ry="4"/><path d="M1 5 H9"/></svg>companyname.com</li>
    </ul>

    <div class="brand">
      <span class="brand__mark"></span>
      <span class="brand__name">CORVAN<br>DESIGN</span>
    </div>

    <div class="signatory">
      <div class="signatory__name">Alex Marlow</div>
      <div class="signatory__role">Deisgnation</div>
    </div>

    <address class="address" style="font-style: normal;">
      Address Line1, Address Line2<br>
      Country - 123456
    </address>
  </main>
</body>
</html>
```